Website for new dental office

I am Dr. Colin Ashford and am building a new dental practice. I specialize in general dentistry. I am young and have a higher end dental practice incorporating very new technologies and would like my website to reflect that. As many dental patients are older, the website must be very easy to navigate. I would like patients to be able to request appointments, and will eventually add on patient information forms (the health history, etc, that you normally fill out in the practice) from my practice management software, so leave an area for that.

Industry/Entity Type

Building

```html
<!DOCTYPE html>
<html lang="en">
<head>
<meta charset="utf-8">
<title>Ashford Dental Clinic</title>
<link rel="stylesheet" href="https://fonts.googleapis.com/css2?family=Open+Sans:ital,wght@0,400;0,600;0,700;1,400&display=swap">
<style>
:root{
  --cyan:#45c3de;
  --cyan-dark:#2fb3d1;
  --ink:#333;
  --text:#777;
  --soft:#f2f1f1;
  --line:#dcdcdc;
  --band:#dff0f4;
  --black:#000;
  --white:#fff;
}
*{box-sizing:border-box;margin:0;padding:0}
html,body{width:1200px;height:2329px;overflow:hidden;background:var(--white)}
body{position:relative;font-family:"Open Sans",Arial,sans-serif;color:var(--ink)}
.abs{position:absolute}

/* header */
.top-rule{left:0;top:0;width:1200px;height:3px;background:var(--cyan)}
.header-rule{left:0;top:133px;width:1200px;height:3px;background:var(--cyan)}
.brand{left:136px;top:52px;font-size:28px;font-weight:700;color:var(--cyan);letter-spacing:.2px}
.nav{left:0;top:62px;font-size:15px;color:var(--cyan)}
.nav a{position:absolute;color:var(--cyan);text-decoration:none;white-space:nowrap}
.nav-marker{left:615px;top:84px}

/* hero */
.hero{left:0;top:136px;width:1200px;height:390px;
  background:linear-gradient(90deg,#d9a28e 0%,#f1d5c8 18%,#c9767a 30%,#e7c1b0 48%,#d98a8e 62%,#f0d6c9 80%,#c98c82 100%)}
.hero-arrow{top:304px;width:23px;height:53px;background:rgba(255,255,255,.75)}
.hero-dots{left:571px;top:504px;display:flex;gap:4px}
.hero-dots span{width:10px;height:10px;border-radius:50%;background:rgba(255,255,255,.6)}
.hero-dots .is-active{background:var(--cyan)}

/* appointment */
.appointment{left:0;top:526px;width:1200px;height:197px;background:var(--soft)}
.section-heading{font-size:24px;font-weight:700}
.field-label{font-size:14px;color:var(--ink)}
.field{height:20px;background:var(--white);border:1px solid #e2e2e2}
.request-btn{left:730px;top:619px;width:315px;height:52px;background:var(--cyan);color:var(--white);
  font-size:23px;display:flex;align-items:center;justify-content:center;border:1px solid #3ab6d1}

/* services */
.cyan-heading{color:var(--cyan);font-weight:700;font-size:23px}
.pager{display:flex;gap:2px}
.pager span{width:33px;height:32px;background:#e6e6e6;border:1px solid #ddd;display:flex;align-items:center;justify-content:center}
.service-card{top:827px;width:308px;height:278px;border:1px solid var(--line);border-radius:3px;text-align:center}
.service-icon{position:absolute;left:98px;top:14px;width:112px;height:112px;border-radius:50%;background:#ebebeb;display:flex;align-items:center;justify-content:center}
.service-title{position:absolute;left:0;top:156px;width:100%;font-size:14px;color:var(--cyan)}
.service-text{position:absolute;left:9px;top:196px;width:288px;font-size:11px;line-height:20.5px;color:var(--text);text-align:justify;text-align-last:center}

/* welcome */
.doctor-photo{left:137px;top:1189px;width:495px;height:337px;border:1px solid var(--line);
  background:linear-gradient(180deg,#ffffff 0%,#f4f6f8 55%,#dfe8f1 100%)}
.welcome-heading{left:654px;top:1207px}
.welcome-text{left:654px;top:1260px;width:399px;font-size:11px;line-height:20.4px;color:var(--text);text-align:justify}

/* testimonials & news */
.band{left:0;top:1619px;width:1200px;height:454px;background:var(--band)}
.panel{top:1655px;width:450px;height:383px;border:1px solid #cfe3e8;background:#e6f3f6}
.panel-heading{position:absolute;left:21px;top:22px;font-size:23px;font-weight:600;color:var(--ink)}
.panel .pager{position:absolute;top:15px;right:22px}
.panel .pager span{width:31px;height:30px;background:#eef6f8}
.entry-name{font-size:13px;font-weight:600;color:var(--ink)}
.entry-text{font-size:11px;line-height:20.4px;color:var(--text)}
.quote{font-size:18px;line-height:0;color:#888}
.avatar{width:82px;height:82px;transform:rotate(45deg);border-radius:4px;background:linear-gradient(135deg,#e9c7ad,#c68e6c)}
.read-more{font-size:11px;font-style:italic;color:var(--ink);text-align:right}

/* footer */
.footer{left:0;top:2073px;width:1200px;height:256px;background:var(--black);color:var(--white)}
.footer-heading{font-size:24px;color:var(--white)}
.footer-small{font-size:12px;line-height:20px;color:var(--white)}
.map{left:132px;top:2130px;width:279px;height:121px;background:linear-gradient(135deg,#e8e4dc,#d9d3c7 60%,#f2d86a)}
.social{display:flex;gap:4px}
.social span{width:23px;height:23px;border-radius:50%;background:var(--white)}
.news-input{left:801px;top:2181px;width:253px;height:24px;background:var(--white);border-radius:6px;color:#999;font-size:11px;padding:4px 9px}
.submit-btn{left:801px;top:2222px;width:95px;height:31px;background:var(--cyan);border-radius:4px;color:var(--white);font-size:17px;display:flex;align-items:center;justify-content:center}
.footer-rule{left:132px;top:2282px;width:936px;height:1px;background:#444}
.copyright{left:0;top:2294px;width:1200px;text-align:center;font-size:11px;color:var(--white)}
</style>
</head>
<body>

<div class="abs top-rule"></div>
<div class="abs brand">Ashford Dental Clinic</div>
<nav class="abs nav">
  <a style="left:615px">Home</a>
  <a style="left:677px">About Us</a>
  <a style="left:759px">Services</a>
  <a style="left:834px">Gallery</a>
  <a style="left:902px">Testimonials</a>
  <a style="left:1006px">Contacts</a>
</nav>
<svg class="abs nav-marker" width="40" height="12" viewBox="0 0 40 12"><path d="M0 0H40V4L20 12L0 4Z" fill="#45c3de"/></svg>
<div class="abs header-rule"></div>

<div class="abs hero" role="img" aria-label="Close-up of three smiling people with bright white teeth"></div>
<div class="abs hero-arrow" style="left:0"><svg width="23" height="53"><path d="M14 16 Q9 26 14 37" stroke="#666" stroke-width="2" fill="none"/></svg></div>
<div class="abs hero-arrow" style="left:1177px"><svg width="23" height="53"><path d="M9 16 Q14 26 9 37" stroke="#666" stroke-width="2" fill="none"/></svg></div>
<div class="abs hero-dots"><span></span><span></span><span class="is-active"></span><span></span><span></span></div>

<section class="abs appointment"></section>
<h2 class="abs section-heading" style="left:152px;top:545px">Quick Appoinment</h2>
<span class="abs field-label" style="left:152px;top:608px">Name</span>
<span class="abs field" style="left:242px;top:609px;width:135px"></span>
<span class="abs field-label" style="left:450px;top:608px">Email</span>
<span class="abs field" style="left:562px;top:609px;width:134px"></span>
<span class="abs field-label" style="left:152px;top:662px">Contact No.</span>
<span class="abs field" style="left:241px;top:663px;width:135px"></span>
<span class="abs field-label" style="left:451px;top:662px">Preffered Date</span>
<span class="abs field" style="left:562px;top:663px;width:134px"></span>
<div class="abs request-btn">Request An Appoinment</div>

<h2 class="abs cyan-heading" style="left:137px;top:771px">Our Services</h2>
<div class="abs pager" style="left:995px;top:765px">
  <span><svg width="10" height="16"><path d="M7 2 Q2 8 7 14" stroke="#fff" stroke-width="2" fill="none"/></svg></span>
  <span><svg width="10" height="16"><path d="M3 2 Q8 8 3 14" stroke="#fff" stroke-width="2" fill="none"/></svg></span>
</div>

<article class="abs service-card" style="left:137px">
  <div class="service-icon"><svg width="60" height="70" viewBox="0 0 60 70"><path d="M14 6C4 6 2 18 5 30C8 42 10 64 17 64C23 64 23 44 30 44C37 44 37 64 43 64C50 64 52 42 55 30C58 18 56 6 46 6C38 6 36 11 30 11C24 11 22 6 14 6Z M16 14L22 24L18 30" fill="none" stroke="#111" stroke-width="3.5" stroke-linejoin="round"/></svg></div>
  <h3 class="service-title" style="font-weight:400">Teeth Crown Fixing</h3>
  <p class="service-text">Sed ut perspiciatis unde omnis iste natus error sit voluptatem accusantium doloremque laudantium, totam rem aperiam, eaque ipsa...</p>
</article>
<article class="abs service-card" style="left:447px">
  <div class="service-icon"><svg width="60" height="70" viewBox="0 0 60 70"><path d="M14 6C4 6 2 18 5 30C8 42 10 64 17 64C23 64 23 44 30 44C37 44 37 64 43 64C50 64 52 42 55 30C58 18 56 6 46 6C38 6 36 11 30 11C24 11 22 6 14 6Z M16 16Q12 30 16 44" fill="none" stroke="#111" stroke-width="3.5" stroke-linejoin="round"/></svg></div>
  <h3 class="service-title" style="font-weight:400">Teeth Whitening</h3>
  <p class="service-text">Sed ut perspiciatis unde omnis iste natus error sit voluptatem accusantium doloremque laudantium, totam rem aperiam, eaque ipsa...</p>
</article>
<article class="abs service-card" style="left:756px">
  <div class="service-icon"><svg width="70" height="70" viewBox="0 0 70 70"><path d="M30 8C20 12 20 24 26 30C30 34 26 40 28 44C30 48 36 44 38 40C40 36 44 38 48 40C56 42 64 32 60 22C56 12 42 4 30 8Z" fill="none" stroke="#111" stroke-width="3.5"/><path d="M28 42L12 62" stroke="#111" stroke-width="4" stroke-dasharray="3 3"/></svg></div>
  <h3 class="service-title" style="font-weight:400">Dental Implants</h3>
  <p class="service-text">Sed ut perspiciatis unde omnis iste natus error sit voluptatem accusantium doloremque laudantium, totam rem aperiam, eaque ipsa...</p>
</article>

<div class="abs doctor-photo" role="img" aria-label="Portrait of a smiling senior dentist in a white coat with a stethoscope"></div>
<h2 class="abs cyan-heading welcome-heading">Welcome !!</h2>
<p class="abs welcome-text">Sed ut perspiciatis unde omnis iste natus error sit voluptatem accusantium doloremque laudantium, totam rem aperiam, eaque ipsa quae ab illo inventore veritatis et quasi architecto beatae vitae dicta sunt explicabo. Nemo enim ipsam voluptatem quia voluptas sit aspernatur aut odit aut fugit, sed quia consequuntur magni dolores eos qui ratione voluptatem sequi nesciunt. Neque porro quisquam est, qui dolorem ipsum quia dolor sit amet, consectetur, adipisci velit, sed quia non numquam eius modi tempora incidunt ut labore et dolore magnam aliquam quaerat voluptatem. Ut enim ad minima veniam, quis nostrum exercitationem ullam corporis suscipit laboriosam, nisi ut aliquid ex ea commodi consequatur? Quis autem vel eum iure reprehenderit qui in ea voluptate velit esse quam nihil molestiae consequatur, vel illum qui dolorem eum fugiat quo voluptas nulla pariatur.</p>

<div class="abs band"></div>

<section class="abs panel" style="left:137px">
  <h2 class="panel-heading">Testimonial</h2>
  <div class="pager">
    <span><svg width="10" height="16"><path d="M7 2 Q2 8 7 14" stroke="#ccc" stroke-width="2" fill="none"/></svg></span>
    <span><svg width="10" height="16"><path d="M3 2 Q8 8 3 14" stroke="#ccc" stroke-width="2" fill="none"/></svg></span>
  </div>
  <div class="abs avatar" style="left:25px;top:106px" role="img" aria-label="Portrait of a smiling young man"></div>
  <div class="abs" style="left:142px;top:86px;width:283px">
    <p class="entry-name">Lorem ipsum</p>
    <p class="entry-text" style="margin-top:4px;text-align:justify"><span class="quote">“</span>adipiscing elit. Etiam quis placerat urna. Nulla nu adipiscing non ornardfe non, commodo non ipsum dolor sit. adipiscing elit. Etiam quis placerat urna. Nulla nu adipiscing.... <span class="quote">”</span></p>
  </div>
  <div class="abs avatar" style="left:25px;top:256px" role="img" aria-label="Portrait of a smiling young girl"></div>
  <div class="abs" style="left:142px;top:236px;width:283px">
    <p class="entry-name">Lorem ipsum</p>
    <p class="entry-text" style="margin-top:4px;text-align:justify"><span class="quote">“</span>adipiscing elit. Etiam quis placerat urna. Nulla nu adipiscing non ornardfe non, commodo non ipsum dolor sit. adipiscing elit. Etiam quis placerat urna. Nulla nu adipiscing.... <span class="quote">”</span></p>
  </div>
</section>

<section class="abs panel" style="left:613px">
  <h2 class="panel-heading">News &amp; Events</h2>
  <div class="pager">
    <span><svg width="10" height="16"><path d="M7 2 Q2 8 7 14" stroke="#ccc" stroke-width="2" fill="none"/></svg></span>
    <span><svg width="10" height="16"><path d="M3 2 Q8 8 3 14" stroke="#ccc" stroke-width="2" fill="none"/></svg></span>
  </div>
  <div class="abs" style="left:22px;top:86px;width:407px">
    <p class="entry-name">Lorem ipsum</p>
    <p class="entry-text" style="margin-top:4px"><span class="quote">“</span>adipiscing elit. Etiam quis placerat urna. Nulla nu adipiscing non ornardfe it. Etiam quis placerat adipiscing.... <span class="quote">”</span></p>
    <p class="read-more" style="margin-top:-20px">Read More</p>
  </div>
  <div class="abs" style="left:22px;top:176px;width:407px">
    <p class="entry-name">Lorem ipsum</p>
    <p class="entry-text" style="margin-top:4px"><span class="quote">“</span>adipiscing elit. Etiam quis placerat urna. Nulla nut. Etiam quis placerat urna. Nulla nu adipiscing.... <span class="quote">”</span></p>
    <p class="read-more" style="margin-top:-20px">Read More</p>
  </div>
  <div class="abs" style="left:22px;top:269px;width:407px">
    <p class="entry-name">Lorem ipsum</p>
    <p class="entry-text" style="margin-top:4px"><span class="quote">“</span>adipiscing elit. Etiam quis placerat urna. Nulla nu adipiscing non ornardfe non, commodo non ipsum placerat urna. Nulla nu adipiscing.... <span class="quote">”</span></p>
    <p class="read-more" style="margin-top:4px">Read More</p>
  </div>
</section>

<footer class="abs footer"></footer>
<h3 class="abs footer-heading" style="left:135px;top:2084px;font-weight:400">Location</h3>
<div class="abs map" role="img" aria-label="Street map showing the clinic location"></div>
<h3 class="abs footer-heading" style="left:540px;top:2083px;font-weight:400">Contact Us</h3>
<p class="abs footer-small" style="left:540px;top:2126px">1.555.210.4478<br>help@ashfordclinic.com</p>
<h3 class="abs footer-heading" style="left:540px;top:2188px;font-weight:400">Follow Us</h3>
<div class="abs social" style="left:540px;top:2230px" aria-label="Social links"><span></span><span></span><span></span><span></span><span></span></div>
<h3 class="abs footer-heading" style="left:801px;top:2083px;font-weight:400">Our Newsletter</h3>
<p class="abs footer-small" style="left:801px;top:2126px;width:270px">Stay ytuned as we give more updates and pffers through Mara Lindqvist</p>
<div class="abs news-input">Enter your email id:</div>
<div class="abs submit-btn">SUBMIT</div>
<div class="abs footer-rule"></div>
<p class="abs copyright">©2014 Ashford Dental Clinic | Privacy Policy | Terms &amp; Conditions</p>

</body>
</html>
```